Basic Commercial & Residential Real Estate Web Site

I need a basic website for a new real estate company that deals with both residential and commercial sales. It must be clean and professional. We sell homes, office buildings, farms, and ranches. It should feel crisp and clean.
I need a main page with my logo and links to commercial, residential, farm and land searches with contact data forms. Also incorporated would be a mls property search (IDX) form. I am in Northern California and the current site I posted is at www.tlvarden.com. I need the functionality of the links and the supporting pages. I do not have all the copy ready because I did not know what to expect.
Updates

Project Deadline Extended
Reason: I apologize, I am extremely busy and you all need more data to do a good job. All the designs are great so far and it is extremely difficult to choose at this point. I haven't given you enough data. I haver now uploaded some relevent photos (not very good) and edited the brief. I am looking for what I call the Landing or main page with some functionality built in to other pages which I also need. Example if you click on "Commercial" it should go to a page that discusses our commercial dept.......

I would like to thank all the designers for all their hard work and efforts, I wish I could reward you all.

Thanks again for your creative and professional designs.

Edwin

Target Market(s)

Corporate Execs for the Commercial Buildings
Homeowners/Families for the Homes and Farms
Upper end people for the land to build estates

Industry/Entity Type

Real Estate

Font styles to use
Sans Serif

Requirements
Must have
• Our Logo should be prominent, pronounced
Need contact data or button
Functional Page that links to other data pages
Must Have a "search for properties" feature
Must say "Commercial and Residential Representation"
Pictures of Commercial Building and Nice Home (Tradtional not contemporary)
Nice to have
• Individual Buttons or links to "Commercial, Residential, Farm/Ranch, Land"
Contact Data displayed
button that says "Maple Crest"-next to button is Maple Crest Logo-see www.maplecrest.bz
Links to "Buyers and "Sellers"
Links to Facebook, twitter,.....etc
Should not have
• 20+ story commercial buildings or ultra modern. See uploaded files of typical buildings for commercial.

```html
<!DOCTYPE html>
<html lang="en">
<head>
<meta charset="utf-8">
<title>Properties by Varden – Home</title>
<link rel="stylesheet" href="https://fonts.googleapis.com/css2?family=Open+Sans:wdth,wght@75..100,300..800&family=PT+Serif&display=swap">
<style>
:root{
  --dark:#2d2d2d;
  --darker:#232323;
  --blue:#1ea3dc;
  --blue-deep:#1f86c0;
  --green:#8aad17;
  --text:#333;
  --muted:#666;
  --line:#9fd6ee;
  --page:#f6f6f6;
  --card:#fff;
  --border:#dcdcdc;
}
*{box-sizing:border-box;margin:0;padding:0}
html,body{width:670px;height:1200px;overflow:hidden}
body{font-family:"Open Sans",Arial,sans-serif;color:var(--text);background:var(--page);position:relative;font-size:7px}
a{color:inherit;text-decoration:none}

.site-header{position:absolute;left:0;top:0;width:670px;height:70px;background:var(--dark)}
.brand{position:absolute;left:56px;top:12px;color:#fff;line-height:1}
.brand-small{display:block;font-size:9px;letter-spacing:1px;margin-left:38px;font-weight:400}
.brand-name{display:block;font-size:34px;font-weight:300;letter-spacing:2px;margin-top:1px}
.account{position:absolute;right:56px;top:20px;font-size:7px;color:var(--green)}
.account span{color:#888;margin:0 3px}
.main-nav{position:absolute;right:56px;top:42px;display:flex}
.main-nav a{color:#fff;font-size:9.5px;padding:6px 7px;height:27px}
.main-nav a.active{background:#fff;color:#111}

.hero{position:absolute;left:0;top:70px;width:670px;height:297px;background:linear-gradient(180deg,#3f7fd3 0%,#7fb2e8 38%,#c9c9c4 58%,#8e8e88 100%)}
.hero-caption{position:absolute;left:345px;top:168px;width:236px;height:104px;background:rgba(255,255,255,.45);text-align:center;line-height:1}
.hero-caption .l1{display:block;color:var(--green);font-size:26px;font-weight:300;margin:-8px 0 0 30px}
.hero-caption .l2{display:block;color:#111;font-size:50px;font-weight:300}
.hero-caption .l3{display:block;color:var(--green);font-size:28px;font-weight:300;margin-left:-10px}
.arrow{position:absolute;width:17px;height:17px;background:#111;display:flex;align-items:center;justify-content:center}

.feature{position:absolute;top:390px;width:162px;height:203px;background:var(--card);border:1px solid var(--border)}
.feature .photo{height:131px;position:relative}
.feature .tag{position:absolute;left:0;bottom:0;width:100%;height:20px;background:rgba(20,20,20,.8);color:var(--blue);font-size:9px;padding:4px 10px;font-weight:600}
.feature p{padding:9px 9px 0;font-size:7px;line-height:1.35}
.more{color:var(--green);font-size:7px}
.feature .more{position:absolute;right:9px;bottom:9px}

.discussions{position:absolute;left:423px;top:390px;width:192px;height:204px;background:#f0f0f0;border:1px solid var(--border);padding:6px}
.discussions h2{font-family:"PT Serif",serif;font-weight:400;font-size:8.5px;text-align:center;background:#fafafa;border:1px solid #ddd;padding:9px 0;margin-bottom:5px}
.post{display:grid;grid-template-columns:18px 1fr 50px;background:#fff;border:1px solid #ddd;margin-bottom:3px;padding:4px 0 3px 8px;font-size:6.5px;line-height:1.7}
.post:nth-child(odd){background:#f7f7f7}
.post .by b{color:var(--green);font-weight:400}
.view-all{position:absolute;left:50%;bottom:0;transform:translateX(-50%);background:#444;color:var(--blue);font-size:6px;padding:3px 14px;border-radius:6px 6px 0 0}

.section-title{position:absolute;top:616px;color:var(--blue);font-weight:700;font-stretch:75%;font-size:15px;border-bottom:1px solid var(--line);padding-bottom:4px}
.work{position:absolute;top:654px;width:123px}
.work .photo{height:90px}
.work p{font-size:6.8px;line-height:1.55;margin-top:7px}
.work .more{float:right}

.search-title{position:absolute;left:56px;top:829px;width:558px;display:flex;align-items:center;gap:6px;color:var(--blue);font-size:12px;font-weight:600}
.search-title::after{content:"";flex:1;height:1px;background:var(--line)}
.search-intro{position:absolute;left:56px;top:853px;font-size:8px}
.search-form{position:absolute;left:56px;top:882px;width:565px;display:grid;grid-template-columns:repeat(5,116px);row-gap:9px}
.field label{display:block;font-size:7px;margin-bottom:3px}
.select{width:93px;height:16px;border:1px solid #bbb;background:#fff;position:relative;font-size:6.5px;padding:3px 8px}
.select::after{content:"";position:absolute;right:0;top:0;width:14px;height:14px;background:#eee;border-left:1px solid #ccc}
.select::before{content:"";position:absolute;right:4px;top:6px;border:3px solid transparent;border-top:4px solid #555;z-index:1}
.search-btn{margin-top:13px;width:62px;height:14px;border-radius:3px;background:linear-gradient(#2aa0d8,#0f6c9e);color:#fff;font-size:6.5px;text-align:center;line-height:14px;border:1px solid #0b5a84}

.site-footer{position:absolute;left:0;top:981px;width:670px;height:189px;background:var(--dark);color:#fff}
.foot-col{position:absolute;top:37px;font-size:7px}
.foot-col h3{display:inline-block;background:var(--blue-deep);font-weight:400;font-size:9px;padding:4px 14px;margin-bottom:10px}
.foot-col li{list-style:none;margin-bottom:9.5px;padding-left:14px;position:relative}
.foot-col li::before{content:"";position:absolute;left:0;top:2px;border:3px solid transparent;border-left:4px solid #fff}
.foot-col p{line-height:1.7;margin-bottom:4px}
.foot-col .link{color:var(--green);border-bottom:1px solid #666;display:inline-block;margin-bottom:16px}
.contact-line{display:flex;align-items:center;gap:6px;margin-top:8px}
.social{display:flex;gap:5px;margin-top:14px}
.social span{width:11px;height:11px;border-radius:50%}
.copyright{position:absolute;left:0;top:1170px;width:670px;height:30px;background:var(--darker);color:#ccc;font-size:6.5px;text-align:center;line-height:30px}
</style>
</head>
<body>

<header class="site-header">
  <a class="brand" href="#">
    <span class="brand-small">PROPERTIES BY</span>
    <span class="brand-name">VARDEN</span>
  </a>
  <div class="account">Welcome Guest<span>|</span>Login<span>|</span>Register FREE</div>
  <nav class="main-nav">
    <a class="active" href="#">HOME</a><a href="#">COMMERCIAL</a><a href="#">RESIDENTIAL</a><a href="#">FORE</a><a href="#">RENT</a><a href="#">CONTACT</a>
  </nav>
</header>

<section class="hero" role="img" aria-label="Traditional two-storey family home with grey siding under a blue sky">
  <span class="arrow" style="left:58px;top:140px"><svg width="6" height="8"><path d="M5 0 1 4l4 4" fill="none" stroke="#fff" stroke-width="1.6"/></svg></span>
  <span class="arrow" style="left:597px;top:140px"><svg width="6" height="8"><path d="M1 0l4 4-4 4" fill="none" stroke="#fff" stroke-width="1.6"/></svg></span>
  <div class="hero-caption"><span class="l1">Lorem</span><span class="l2">Ipsum</span><span class="l3">simply</span></div>
</section>

<article class="feature" style="left:56px">
  <div class="photo" role="img" aria-label="Large traditional estate home beside a lake" style="background:linear-gradient(180deg,#6fa4dc 0%,#b8cfe0 45%,#c9c3b0 62%,#5d7f5a 100%)"><span class="tag">COMMERCIAL</span></div>
  <p>Lorem Ipsum is simply dummy text of the printing and typesetting<br>Lorem Ipsum is simply dummy text of the printing and typesetting</p>
  <a class="more" href="#">Read more.....</a>
</article>
<span class="arrow" style="left:52px;top:450px"><svg width="6" height="8"><path d="M5 0 1 4l4 4" fill="none" stroke="#fff" stroke-width="1.6"/></svg></span>

<article class="feature" style="left:230px">
  <div class="photo" role="img" aria-label="Low-rise glass and brick office building" style="background:linear-gradient(135deg,#e2e6ea 0%,#a08070 35%,#3c4c5a 60%,#1d2630 100%)"><span class="tag">FARM</span></div>
  <p>Lorem Ipsum is simply dummy text of the printing and typesetting<br>Lorem Ipsum is simply dummy text of the printing and typesetting</p>
  <a class="more" href="#">Read more.....</a>
</article>
<span class="arrow" style="left:379px;top:450px"><svg width="6" height="8"><path d="M1 0l4 4-4 4" fill="none" stroke="#fff" stroke-width="1.6"/></svg></span>

<aside class="discussions">
  <h2>LATEST DISCUSSIONS:</h2>
  <div>
    <div class="post"><svg width="9" height="7"><ellipse cx="4.5" cy="3" rx="4" ry="2.6" fill="#555"/><path d="M2 5 1 7l3-1.5z" fill="#555"/></svg><span>Lorem Ipsum is simply dummy<br><span class="by">by : <b>Ipsum</b></span></span><span><br>26-03-2014</span></div>
    <div class="post"><svg width="9" height="7"><ellipse cx="4.5" cy="3" rx="4" ry="2.6" fill="#555"/><path d="M2 5 1 7l3-1.5z" fill="#555"/></svg><span>Lorem Ipsum is simply dummy<br><span class="by">by : <b>Ipsum</b></span></span><span><br>26-03-2014</span></div>
    <div class="post"><svg width="9" height="7"><ellipse cx="4.5" cy="3" rx="4" ry="2.6" fill="#555"/><path d="M2 5 1 7l3-1.5z" fill="#555"/></svg><span>Lorem Ipsum is simply dummy<br><span class="by">by : <b>Ipsum</b></span></span><span><br>26-03-2014</span></div>
    <div class="post"><svg width="9" height="7"><ellipse cx="4.5" cy="3" rx="4" ry="2.6" fill="#555"/><path d="M2 5 1 7l3-1.5z" fill="#555"/></svg><span>Lorem Ipsum is simply dummy<br><span class="by">by : <b>Ipsum</b></span></span><span><br>26-03-2014</span></div>
  </div>
  <a class="view-all" href="#">VIEW ALL POSTS</a>
</aside>

<h2 class="section-title" style="left:56px;width:390px">LATEST WORK</h2>
<h2 class="section-title" style="left:473px;width:141px">OUR SERVICES</h2>

<article class="work" style="left:56px">
  <div class="photo" role="img" aria-label="Two-storey brick office building" style="background:linear-gradient(180deg,#c8d8e8 0%,#e8eef2 40%,#9a6a52 60%,#7a8a70 100%)"></div>
  <p>Lorem Ipsum is simply dummy text of the printing and typesetting Lorem Ipsum text the printing and typesettingLoremy text <a class="more" href="#">Read more...</a></p>
</article>
<article class="work" style="left:190px">
  <div class="photo" role="img" aria-label="Traditional estate home by the water" style="background:linear-gradient(180deg,#6fa4dc 0%,#c0d3e2 45%,#c9c3b0 62%,#5d7f5a 100%)"></div>
  <p>Lorem Ipsum is simply dummy text of the printing and typesetting Lorem Ipsum text the printing and typesettingLoremy text <a class="more" href="#">Read more...</a></p>
</article>
<article class="work" style="left:323px">
  <div class="photo" role="img" aria-label="Cheerful office team celebrating a sale" style="background:linear-gradient(180deg,#f2f2f2 0%,#d8c8b8 50%,#8a8a90 100%)"></div>
  <p>Lorem Ipsum is simply dummy text of the printing and typesetting Lorem Ipsum text the printing and typesettingLoremy text <a class="more" href="#">Read more...</a></p>
</article>
<span class="arrow" style="left:52px;top:697px"><svg width="6" height="8"><path d="M5 0 1 4l4 4" fill="none" stroke="#fff" stroke-width="1.6"/></svg></span>
<span class="arrow" style="left:434px;top:705px"><svg width="6" height="8"><path d="M1 0l4 4-4 4" fill="none" stroke="#fff" stroke-width="1.6"/></svg></span>
<article class="work" style="left:472px;width:142px">
  <div class="photo" role="img" aria-label="Group of business professionals in suits" style="background:linear-gradient(180deg,#f4f4f4 0%,#c8c8c8 50%,#3a3a40 100%)"></div>
  <p>Lorem Ipsum is simply dummy text of the printing and typesetting Lorem Ipsum text the printing and typesettin-gLoremy text <a class="more" href="#">Read more...</a></p>
</article>

<h2 class="search-title">FIND YOUR NEW HOME</h2>
<p class="search-intro">9 Real Estate Listings, Homes for Sale &amp; Rental Properties.</p>
<form class="search-form">
  <div class="field"><label>Type</label><div class="select">Any</div></div>
  <div class="field"><label>City</label><div class="select">Any</div></div>
  <div class="field"><label>State</label><div class="select">Any</div></div>
  <div class="field"><label>Zipcode</label><div class="select">Any</div></div>
  <div class="field"><label>Beds</label><div class="select">Any</div></div>
  <div class="field"><label>Baths</label><div class="select">Any</div></div>
  <div class="field"><label>Status</label><div class="select">Any</div></div>
  <div class="field"><label>Price From ($)</label><div class="select"></div></div>
  <div class="field"><label>Price To ($)</label><div class="select"></div></div>
  <div class="field"><div class="search-btn">SEARCH</div></div>
</form>

<footer class="site-footer">
  <div class="foot-col" style="left:56px">
    <h3>Quick link</h3>
    <ul><li>Home</li><li>Commercial</li><li>Residential</li><li>Fore</li><li>Rent</li><li>Contact</li></ul>
  </div>
  <div class="foot-col" style="left:195px">
    <h3>About Us</h3>
    <ul><li>Lorem Ipsum</li><li>Lorem Ipsum</li><li>Lorem Ipsum</li><li>Lorem Ipsum</li><li>Lorem Ipsum</li><li>Lorem Ipsum</li></ul>
  </div>
  <div class="foot-col" style="left:323px;width:130px">
    <h3>Blog</h3>
    <p>Lorem Ipsum is simply dummy text of the printing and typesetting</p>
    <a class="link" href="#">industry's standard industry's stan-</a>
    <p>Lorem Ipsum is simply dummy text of the printing and typesetting</p>
    <a class="link" href="#">industry's standard dard</a>
  </div>
  <div class="foot-col" style="left:496px;width:125px">
    <h3>Contact Us</h3>
    <p>Lorem Ipsum is simply dummy text of the printing and typesetting of the printing and typesetting</p>
    <div class="contact-line"><svg width="6" height="8"><rect x="0.5" y="0.5" width="5" height="7" rx="1" fill="none" stroke="#fff"/></svg> : +91-0155-482-730</div>
    <div class="contact-line"><svg width="10" height="7"><rect x="0.5" y="0.5" width="9" height="6" fill="none" stroke="#fff"/><path d="M.5.5 5 4l4.5-3.5" fill="none" stroke="#fff"/></svg> : tlvarden.mail</div>
    <div class="social"><span style="background:#3b5b99"></span><span style="background:#2fa6de"></span><span style="background:#1f78b0"></span><span style="background:#d44a35"></span></div>
  </div>
</footer>
<div class="copyright">Copyright © 2014 . All rights reserved.</div>

</body>
</html>
```